Redesign Two Website Pages (Homepage & Features) — Modern, Responsive, and Visually Engaging

We’re looking to redesign two pages of our website:

Homepage: https://velmorta.com
Features Page: https://velmorta.com/features

We already have a preliminary design in Figma for the homepage, but it currently feels too plain. Please don’t use this Figma file provided. It was only shared for facilitate using the current website content and not as a source for inspiration. Use your creativity to bring something fresh and less dull as the current design.

We want to enhance it with visually engaging elements, such as illustrations, graphics, or images that align with the content and the application’s purpose, making the design more dynamic and marketing-oriented.

Requirements:
- Create modern, visually appealing designs for both pages.
- Include relevant visuals (images or vector graphics) that complement the content and improve user engagement.
- Ensure full responsiveness across all major viewports: desktop, tablet, and mobile.
- Deliver the final design in Figma format.
- You can choose any colour palette that best fits the concept, but please retain the existing content from the live website.
- We’re looking for a clean, modern, and commercially appealing design that effectively communicates the value of our product.

Target Market(s)

B2B

Number of Pages Required

2 page

Font styles to use
Sans Serif

Requirements
Must have
• Images and graphics to make the design and product more attractive.

```html
<!DOCTYPE html>
<html lang="en">
<head>
<meta charset="utf-8">
<title>VELMORTA — Guiding every audit with clarity</title>
<link href="https://fonts.googleapis.com/css2?family=Lato:ital,wght@0,400;0,700;0,900;1,400&display=swap" rel="stylesheet">
<style>
:root{
  --blue:#1553c9;
  --blue-deep:#0a2f9e;
  --blue-bright:#1a73e8;
  --navy:#0b1830;
  --ink:#111827;
  --muted:#4b5563;
  --line:#e5e7eb;
  --white:#ffffff;
  --red:#d32f2f;
  --green:#22a04b;
  --star:#f5b301;
}
*{box-sizing:border-box;margin:0;padding:0}
html,body{width:1200px;height:5038px;overflow:hidden}
body{font-family:'Lato',sans-serif;color:var(--ink);background:var(--white);position:relative}
.abs{position:absolute}
.center{text-align:center;left:0;right:0}

/* nav */
.nav{position:absolute;top:0;left:0;width:1200px;height:70px;background:var(--white);box-shadow:0 1px 4px rgba(0,0,0,.06);z-index:5}
.brand{position:absolute;left:143px;top:14px;display:flex;gap:10px;align-items:center}
.brand-mark{width:22px;height:22px;background:var(--blue)}
.brand-name{font-weight:700;font-size:17px;line-height:1}
.brand-tag{font-size:11px;color:var(--muted);margin-top:3px}
.nav-links{position:absolute;left:512px;top:24px;display:flex;gap:30px;font-size:14px;font-weight:700}
.nav-links .active{color:var(--blue)}
.nav-btns{position:absolute;left:844px;top:12px;display:flex;gap:6px}
.btn-sm{height:44px;padding:0 16px;border-radius:5px;font-size:14px;font-weight:700;display:flex;align-items:center;gap:6px}
.btn-outline{border:2px solid var(--blue);color:var(--blue);background:var(--white)}
.btn-fill{background:var(--blue);color:var(--white)}

/* hero */
.hero{position:absolute;top:70px;left:0;width:1200px;height:790px;background:linear-gradient(90deg,#2a6fe0,#0a2f9e);overflow:hidden}
.hero-dark{position:absolute;inset:0;background:var(--navy);clip-path:polygon(0 0,100% 0,100% 50%,30.6% 87.6%,0 61%)}
.hero-photo{position:absolute;left:470px;top:0;width:730px;height:790px;background:linear-gradient(110deg,#0b1830 0%,#3a4a5e 25%,#8d99a8 55%,#c9d0d8 80%,#e4e8ec 100%)}
.hero-white{position:absolute;left:0;top:0}
.hero-copy{position:absolute;left:143px;top:100px;width:480px;color:var(--white)}
.hero-kicker{color:#3d8bff;font-size:13px;margin-bottom:14px}
.hero h1{font-size:43px;line-height:1.1;font-weight:700}
.hero p{font-size:14px;line-height:1.7;margin-top:14px}
.hero-ctas{display:flex;gap:12px;margin-top:20px}
.btn{height:42px;padding:0 26px;border-radius:5px;font-size:14px;font-weight:700;display:flex;align-items:center}
.btn-blue{background:var(--blue);color:var(--white)}
.btn-white{background:var(--white);color:var(--ink)}
.hero-note{font-size:13px;margin-top:18px}
.hero-arrows{display:flex;gap:8px;margin-top:28px}
.circle-btn{width:32px;height:32px;border-radius:50%;background:var(--white);display:flex;align-items:center;justify-content:center}

/* stats */
.stats{position:absolute;top:895px;left:143px;width:914px;display:flex}
.stat{flex:1;display:flex;gap:14px}
.stat+.stat{border-left:2px solid var(--line);padding-left:48px}
.dot{width:18px;height:18px;border-radius:50%;background:var(--blue);margin-top:12px}
.stat-num{font-size:26px;font-weight:700}
.stat-lbl{font-size:15px;color:var(--muted);margin-top:4px}

/* problem */
.h2{font-size:38px;font-weight:700;line-height:1.25}
.sub{font-size:14px;color:var(--muted)}
.compare-card{position:absolute;background:var(--white);border-radius:10px;box-shadow:0 8px 30px rgba(20,40,90,.1);padding:48px 48px}
.compare-card h3{font-size:26px;font-weight:700;margin-bottom:30px}
.compare-card li{list-style:none;font-size:13.5px;display:flex;gap:18px;margin-bottom:22px}
.compare-card.with{border-left:6px solid var(--blue);border-bottom:6px solid var(--blue-deep);border-top:6px solid var(--blue-bright);border-radius:16px;padding-top:70px}

/* features */
.features{position:absolute;top:1670px;left:0;width:1200px;height:958px;background:linear-gradient(160deg,#f4f7fc,#e8eef8)}
.grid{position:absolute;left:143px;top:230px;width:912px;display:grid;grid-template-columns:repeat(3,1fr);background:var(--white)}
.cell{height:303px;padding:30px 30px;border:1px solid #eef0f4}
.cell svg{display:block;margin-bottom:22px}
.cell h4{font-size:19px;font-weight:700;margin-bottom:16px}
.cell p{font-size:13.5px;line-height:1.75;color:var(--muted);margin-bottom:14px}
.cell a{font-size:13.5px;color:var(--blue);text-decoration:underline}
.cell.hot{background:linear-gradient(180deg,var(--blue-bright),var(--blue-deep));color:var(--white);margin-top:-10px;height:313px;box-shadow:0 10px 25px rgba(10,47,158,.35)}
.cell.hot p,.cell.hot a{color:var(--white)}

/* testimonial */
.testimonial{position:absolute;top:2628px;left:0;width:1200px;height:577px;background:linear-gradient(135deg,#1a5fd6,#0a3fb0);color:var(--white)}
.testimonial .quote{font-size:18px;font-style:italic;line-height:1.75;width:620px;margin:0 auto}

/* pricing */
.toggle{position:absolute;left:487px;top:3425px;width:226px;height:46px;border:2px solid var(--blue);border-radius:23px;display:flex;align-items:center;padding:3px;font-size:15px;font-weight:700}
.toggle span{flex:1;text-align:center;height:36px;line-height:36px;border-radius:18px}
.toggle .on{background:var(--blue);color:var(--white)}
.slider{position:absolute;left:300px;top:3524px;width:600px;height:6px;border-radius:3px;background:#e4e7ec}
.plans{position:absolute;left:143px;top:3576px;width:914px;display:flex;gap:17px}
.plan{flex:1;height:512px;background:var(--white);border-radius:10px;box-shadow:0 4px 18px rgba(20,40,90,.12);padding:10px;position:relative}
.plan-head{background:#dbe8fb;border-radius:8px;padding:14px 16px;height:138px;font-size:11px;color:var(--muted)}
.plan-head.dark{background:linear-gradient(180deg,var(--blue-bright),var(--blue-deep));color:var(--white)}
.tag{display:inline-block;background:var(--white);color:var(--blue);font-size:10px;padding:3px 8px;border-radius:3px;margin-bottom:8px}
.plan-head.dark .tag{background:rgba(255,255,255,.2);color:var(--white)}
.price{font-size:20px;font-weight:700;color:var(--blue);margin:6px 0 4px}
.plan-head.dark .price{color:var(--white)}
.price small{font-size:12px;font-weight:400}
.plan ul{list-style:none;padding:14px 8px;font-size:11px;color:var(--muted)}
.plan li{margin-bottom:10px;display:flex;gap:10px}
.plan li::before{content:"✓";color:var(--blue);font-weight:900}
.plan li.no::before{content:"✕";color:var(--ink)}
.plan .cta{position:absolute;left:22px;right:22px;bottom:26px;height:42px;border:2px solid var(--blue);border-radius:5px;font-size:13px;font-weight:700;display:flex;align-items:center;justify-content:center}
.plan .cta.solid{background:var(--blue);color:var(--white)}

/* cta */
.cta-band{position:absolute;top:4250px;left:143px;width:914px;height:410px;background:linear-gradient(180deg,var(--blue-bright),var(--blue-deep));color:var(--white);z-index:2}
.cta-frame{position:absolute;inset:22px;border:2px solid rgba(255,255,255,.85)}

/* footer */
.footer{position:absolute;top:4650px;left:0;width:1200px;height:388px;background:#08090d;color:var(--white)}
.fcol{position:absolute;top:104px;font-size:14px}
.fcol h5{font-size:18px;font-weight:700;margin-bottom:22px}
.fcol li{list-style:none;margin-bottom:10px}
.fcol li::before{content:"»";margin-right:12px}
</style>
</head>
<body>

<header class="nav">
  <div class="brand">
    <div class="brand-mark"></div>
    <div><div class="brand-name">VELMORTA</div><div class="brand-tag">Guiding every audit with clarity</div></div>
  </div>
  <nav class="nav-links"><span class="active">Home</span><span>Features</span><span>Pricing</span><span>Demo</span></nav>
  <div class="nav-btns"><span class="btn-sm btn-outline">→ Sign Up</span><span class="btn-sm btn-fill">→ Sign In</span></div>
</header>

<section class="hero">
  <div class="hero-dark">
    <div class="hero-photo" role="img" aria-label="Photo of two business professionals in suits discussing an audit in a bright office"></div>
  </div>
  <svg class="hero-white" width="1200" height="790" viewBox="0 0 1200 790" aria-hidden="true">
    <polygon points="0,505 367,790 0,790" fill="#ffffff"/>
    <polygon points="367,790 1200,460 1200,790" fill="#ffffff"/>
  </svg>
  <div class="hero-copy">
    <div class="hero-kicker">Trusted by 300+ audit firms worldwide</div>
    <h1>Cut audit time by 60% without cutting corners</h1>
    <p>The only audit platform that combines AI powered template generation, real time collaboration, and intelligent compliance tracking. Join leading firms completing audits 3x faster with 99.9% accuracy.</p>
    <div class="hero-ctas"><span class="btn btn-blue">Start 14-day free trial</span><span class="btn btn-white">Schedule demo</span></div>
    <div class="hero-note">No credit card required • 14-day free trial • Cancel anytime</div>
    <div class="hero-arrows">
      <span class="circle-btn"><svg width="12" height="12" viewBox="0 0 12 12"><path d="M8 2 4 6l4 4" stroke="#111" stroke-width="2" fill="none"/></svg></span>
      <span class="circle-btn"><svg width="12" height="12" viewBox="0 0 12 12"><path d="M4 2l4 4-4 4" stroke="#111" stroke-width="2" fill="none"/></svg></span>
    </div>
  </div>
</section>

<div class="stats">
  <div class="stat"><span class="dot"></span><div><div class="stat-num">300+</div><div class="stat-lbl">Audit firms</div></div></div>
  <div class="stat"><span class="dot"></span><div><div class="stat-num">1000+</div><div class="stat-lbl">Audits completed</div></div></div>
  <div class="stat"><span class="dot"></span><div><div class="stat-num">99.9%</div><div class="stat-lbl">Compliance rate</div></div></div>
  <div class="stat"><span class="dot"></span><div><div class="stat-num">4.9/5</div><div class="stat-lbl">Customer rating</div></div></div>
</div>

<h2 class="abs center h2" style="top:1035px">Stop losing <span style="color:var(--blue)">$50K+</span> per year<br>on manual Audits</h2>
<p class="abs center sub" style="top:1144px">Your team spends 70% of audit time on repetitive tasks. We fix that.</p>

<div class="compare-card" style="left:188px;top:1221px;width:430px;height:313px">
  <h3>Without VELMORTA</h3>
  <ul>
    <li><span style="color:var(--red)">✖</span>200+ hours creating templates from scratch</li>
    <li><span style="color:var(--red)">✖</span>Version control chaos with shared spreadsheets</li>
    <li><span style="color:var(--red)">✖</span>60% error rate from manual data entry</li>
    <li><span style="color:var(--red)">✖</span>Compliance violations risk $100K+ fines</li>
  </ul>
</div>
<div class="compare-card with" style="left:603px;top:1188px;width:418px;height:381px">
  <h3>With VELMORTA:</h3>
  <ul>
    <li><span style="color:var(--green)">✔</span>AI generates templates in 30 seconds</li>
    <li><span style="color:var(--green)">✔</span>Real-time collaboration with audit trail</li>
    <li><span style="color:var(--green)">✔</span>Automated validation catches 99% of errors</li>
    <li><span style="color:var(--green)">✔</span>Built-in compliance for ISO, GDPR, PCI DSS</li>
  </ul>
</div>

<section class="features">
  <h2 class="abs center h2" style="top:76px">Everything You Need to Scale<br>Your Audit Practice</h2>
  <p class="abs center sub" style="top:185px">From solo practitioners to Big 4 firms, we ve built the features that matter.</p>
  <div class="grid">
    <div class="cell"><svg width="52" height="52" viewBox="0 0 52 52" fill="none" stroke="#1553c9" stroke-width="2"><circle cx="26" cy="26" r="16"/><text x="18" y="31" font-size="13" fill="#1553c9" stroke="none" font-family="Lato">AI</text></svg><h4>AI-Powered Templates</h4><p>Generate industry-specific audit templates in 30 seconds. Our AI knows ISO 27001, GDPR, PCI DSS, and 50+ frameworks.</p><a>Save 200+ hours per year</a></div>
    <div class="cell hot"><svg width="52" height="52" viewBox="0 0 52 52" fill="none" stroke="#fff" stroke-width="2"><circle cx="20" cy="18" r="8"/><path d="M6 42c0-9 6-14 14-14s14 5 14 14"/><circle cx="34" cy="16" r="6"/><path d="M36 28c6 1 10 6 10 12"/></svg><h4>Real time collaboration</h4><p>Your entire team works together seamlessly. See changes instantly, leave comments, and track who did what.</p><a>3x faster team audits</a></div>
    <div class="cell"><svg width="52" height="52" viewBox="0 0 52 52" fill="none" stroke="#1553c9" stroke-width="2"><rect x="6" y="8" width="26" height="34"/><path d="M12 18h14M12 24h10M12 30h8"/><circle cx="36" cy="22" r="9"/><path d="M42 29l7 8"/></svg><h4>Evidence management</h4><p>Attach documents, screenshots, and recordings directly to audit items. Never lose critical evidence again.</p><a>100% audit trail coverage</a></div>
    <div class="cell"><svg width="52" height="52" viewBox="0 0 52 52" fill="none" stroke="#1553c9" stroke-width="2"><circle cx="26" cy="22" r="14"/><circle cx="26" cy="22" r="5"/><path d="M18 40h16M20 46h12"/></svg><h4>Automated workflows</h4><p>Set up once, run forever. Automated reminders, status updates, and report generation keep projects</p><a>Zero missed deadlines</a></div>
    <div class="cell"><svg width="52" height="52" viewBox="0 0 52 52" fill="none" stroke="#1553c9" stroke-width="2"><circle cx="30" cy="18" r="11"/><path d="M22 26 8 42"/><path d="M25 20l4 3 6-8"/></svg><h4>Smart analytics</h4><p>Spot risks before they become issues. Our dashboard shows completion rates, bottlenecks, and compliance gaps.</p><a>60% fewer compliance issues</a></div>
    <div class="cell"><svg width="52" height="52" viewBox="0 0 52 52" fill="none" stroke="#1553c9" stroke-width="2"><path d="M26 6l16 6v12c0 11-7 18-16 22C17 42 10 35 10 24V12z"/><rect x="20" y="22" width="12" height="10"/><path d="M22 22v-4a4 4 0 0 1 8 0v4"/></svg><h4>Bank-grade security</h4><p>End to end encryption, role-based access, and complete audit logs protect your data.</p><a>Zero security breaches</a></div>
  </div>
</section>

<section class="testimonial">
  <h2 class="abs center h2" style="top:96px">Audit leaders choose VELMORTA</h2>
  <p class="abs center" style="top:156px;font-size:14px">See why we re rated 4.9/5 by 500+ audit professionals.</p>
  <div class="abs center" style="top:248px;color:var(--star);font-size:20px;letter-spacing:4px">★★★★★</div>
  <p class="abs center quote" style="top:286px">“We ve reduced audit completion time from 3 weeks to 1 week. The AI templates alone saved us $200K in the first year. This is a game changer for mid size firms.”</p>
  <div class="abs center" style="top:402px;font-size:25px;font-weight:700">Maren Holt</div>
  <div class="abs center" style="top:440px;font-size:14px">Partner, Holt &amp; Partners CPA</div>
  <svg class="abs" style="left:142px;top:278px" width="36" height="24" viewBox="0 0 36 24"><path d="M34 12H3M12 3 3 12l9 9" stroke="#fff" stroke-width="2.5" fill="none"/></svg>
  <svg class="abs" style="left:1020px;top:278px" width="36" height="24" viewBox="0 0 36 24"><path d="M2 12h31M24 3l9 9-9 9" stroke="#fff" stroke-width="2.5" fill="none"/></svg>
</section>

<p class="abs center" style="top:3306px;color:var(--blue);font-size:14px;font-weight:700">Save 21% with annual billing</p>
<h2 class="abs center h2" style="top:3330px">Simple Pricing That Scales With You</h2>
<p class="abs center sub" style="top:3390px">Choose the perfect plan for your audit team. All plans include a 14-day free trial.</p>
<div class="toggle"><span>Monthly</span><span class="on">Annual</span></div>
<p class="abs center" style="top:3499px;font-size:12px;color:var(--muted)">Team Size: 1 users</p>
<div class="slider"><span class="abs" style="left:0;top:-5px;width:16px;height:16px;border-radius:50%;background:var(--blue);border:3px solid #fff;box-shadow:0 0 0 1px #ccd"></span></div>
<span class="abs" style="left:300px;top:3540px;font-size:11px;color:var(--muted)">1 user</span>
<span class="abs" style="left:832px;top:3540px;font-size:11px;color:var(--muted)">200+ users</span>

<div class="plans">
  <div class="plan">
    <div class="plan-head"><span class="tag">FREE</span><div>Perfect for getting started with basic auditing needs</div><div class="price">$0<small>/month</small></div><div>Up to 2 team members</div></div>
    <ul><li>2 team members</li><li>5 templates</li><li>10 active projects</li><li>Evidence management</li><li>Basic support</li><li class="no">Custom templates</li><li class="no">Advanced analytics</li><li class="no">Priority support</li></ul>
    <span class="cta">Get started for free</span>
  </div>
  <div class="plan">
    <div class="plan-head dark"><span class="tag">STARTER</span><div>Perfect for small audit teams and solo practitioners</div><div class="price">$15<small>/month (billed annually)</small></div><div>$15/user × 1 users 21% off</div></div>
    <ul><li>Unlimited team members</li><li>10 active audits</li><li>Custom templates</li><li>Evidence management</li><li>Email support</li><li class="no">Custom workflows</li><li class="no">Advanced analytics</li><li class="no">Dedicated account manager</li></ul>
    <span class="cta solid">Get started for free</span>
  </div>
  <div class="plan">
    <div class="plan-head"><span class="tag">PROFESSIONAL</span><div>Ideal for growing audit firms with multiple clients</div><div class="price">$39<small>/month (billed annually)</small></div><div>$39/user × 1 users 21% off</div></div>
    <ul><li>Unlimited team members</li><li>Unlimited audits</li><li>Custom templates + AI builder</li><li>Evidence management</li><li>Templates library</li><li>Advanced evidence management</li><li>AI powered scoring analysis</li><li>Priority support</li><li>Custom workflows</li><li>Advanced analytics</li><li>PII detection</li><li class="no">Dedicated account manager</li></ul>
    <span class="cta">Get started for free</span>
  </div>
  <div class="plan">
    <div class="plan-head"><span class="tag">ENTERPRISE</span><div>For large organizations with complex requirements</div><div class="price">Custom <small style="color:var(--ink)">pricing</small></div></div>
    <ul><li>Unlimited team members</li><li>Unlimited audits</li><li>All features included</li><li>Templates library</li><li>AI-powered scoring analysis</li><li>Enterprise security</li><li>Regional compliance</li><li>Data residency guaranteed</li><li>Custom workflows</li><li>Advanced analytics</li><li>PII detection</li><li>Dedicated account manager</li></ul>
    <span class="cta">Contact Sales</span>
  </div>
</div>
<p class="abs center" style="top:4118px;font-size:14px;color:var(--muted)">All plans include: SSL encryption, daily backups, 99.9% uptime SLA</p>

<section class="cta-band">
  <div class="cta-frame"></div>
  <h2 class="abs center h2" style="top:82px">Ready to Transform Your<br>Audit Practice?</h2>
  <p class="abs center" style="top:192px;font-size:14px;line-height:1.7">Join 300+ firms saving millions on audit costs. Start your free trial today and<br>see results in your first audit.</p>
  <div class="abs" style="left:258px;top:264px;display:flex;gap:10px">
    <span class="btn btn-blue" style="border:2px solid #fff;width:196px;justify-content:center">Start 14-day free trial</span>
    <span class="btn btn-white" style="width:196px;justify-content:center">Schedule demo</span>
  </div>
  <p class="abs center" style="top:330px;font-size:14px">No credit card required • 14-day free trial • Cancel anytime</p>
</section>

<footer class="footer">
  <svg class="abs" style="left:0;top:0" width="1200" height="388" viewBox="0 0 1200 388" aria-hidden="true">
    <polygon points="0,0 143,0 143,10 0,50" fill="#1553c9"/>
    <polygon points="1057,0 1200,0 1200,60 1057,10" fill="#1553c9"/>
  </svg>
  <div class="abs" style="left:166px;top:90px;display:flex;gap:10px;align-items:center">
    <div class="brand-mark"></div>
    <div><div style="font-size:20px;font-weight:700">VELMORTA</div><div style="font-size:14px">Guiding every audit with clarity</div></div>
  </div>
  <div class="abs" style="left:166px;top:154px;font-size:14px">Guiding every audit with clarity.</div>
  <div class="fcol" style="left:520px"><h5>Product</h5><ul><li>Features</li><li>Pricing</li><li>Demo</li><li>Sign In</li></ul></div>
  <div class="fcol" style="left:703px"><h5>Company</h5><ul><li>About</li><li>Contact</li><li>System Status</li></ul></div>
  <div class="fcol" style="left:889px"><h5>Legal</h5><ul><li>Privacy Policy</li><li>Terms of Service</li><li>Security</li><li>Compliance</li></ul></div>
  <div class="abs center" style="top:314px;font-size:14px">© 2025 VELMORTA™ - All rights reserved.</div>
</footer>

</body>
</html>
```